Verlindo Magician

I want the business card for my business to give to people who watch that later I will be employed to show magic here is my website http://www.balsamomagicien.com/I want the interesting design , i am very opened for formal and informal, I watch a lot of design so don't stick to the common shape and form but i hope it can also be produced the thing to write on will be the same as in picture that i will upload , i also will upload the logo for you that so can be easy to useDenis CostilleMagicianMAGICIAN VERLINDO 17 rue des Tilleuls - 25000 BESANÇON contact@verlindoillusions.example tel. 0381 946 157 tel. 0674 219 503

```html
<!DOCTYPE html>
<html lang="en">
<head>
<meta charset="utf-8">
<title>Verlindo Magician – Business Card</title>
<link rel="stylesheet" href="https://fonts.googleapis.com/css2?family=Jost:wght@300;400;500&display=swap">
<style>
  :root {
    --bg: #e9e6e1;
    --card: #ffffff;
    --ink: #1a1a1a;
    --muted: #4a4a4a;
    --red: #e0262c;
    --rule: #bdbdbd;
    --pink: #f9dede;
    --suit-grey: #e4e4e4;
  }
  * { margin: 0; padding: 0; box-sizing: border-box; }
  html, body { width: 1200px; height: 1040px; overflow: hidden; }
  body {
    background: var(--bg);
    font-family: "Jost", "Futura", sans-serif;
    color: var(--ink);
    position: relative;
  }
  .card {
    position: absolute;
    left: 200px;
    width: 800px;
    height: 460px;
    background: var(--card);
    box-shadow: 0 6px 18px rgba(0,0,0,.18);
    overflow: hidden;
  }
  .card--front { top: 40px; }
  .card--back { top: 540px; }

  /* front */
  .brand {
    position: absolute;
    right: 60px;
    top: 36px;
    width: 230px;
    text-align: center;
  }
  .brand__illustration {
    width: 150px;
    height: 130px;
    margin: 0 auto 10px;
    background: linear-gradient(160deg, #3a3a3a, #111 70%);
    border-radius: 6px;
  }
  .brand__name {
    font-size: 24px;
    font-weight: 400;
    letter-spacing: 1px;
    color: var(--ink);
  }
  .divider {
    position: absolute;
    left: 290px;
    right: 40px;
    top: 232px;
    height: 1px;
    background: var(--rule);
  }
  .business {
    position: absolute;
    right: 40px;
    top: 250px;
    text-align: right;
    line-height: 1.25;
  }
  .business__title { color: var(--red); font-size: 18px; font-weight: 400; }
  .business__address { color: var(--muted); font-size: 18px; font-weight: 300; }

  .person {
    position: absolute;
    left: 50px;
    top: 230px;
    width: 330px;
  }
  .person__name { font-size: 36px; font-weight: 400; line-height: 1.1; }
  .person__role { color: var(--red); font-size: 22px; font-weight: 400; }
  .person__rule { height: 1px; background: var(--rule); margin: 10px 0 10px; width: 300px; }
  .contact { list-style: none; font-size: 19px; font-weight: 300; color: var(--muted); line-height: 1.35; }
  .contact li { display: flex; align-items: center; gap: 10px; }
  .contact svg { width: 16px; height: 16px; flex: none; }

  .band { position: absolute; left: 0; bottom: 0; width: 800px; height: 70px; }
  .band__url {
    position: absolute;
    right: 30px;
    bottom: 18px;
    color: #fff;
    font-size: 19px;
    font-weight: 400;
    letter-spacing: .5px;
  }

  /* back */
  .suit-pattern {
    position: absolute;
    inset: 0;
    background: linear-gradient(135deg, var(--pink), #f4f1f1 50%, var(--suit-grey));
    opacity: .8;
  }
  .back__illustration {
    position: absolute;
    left: 290px;
    top: 110px;
    width: 220px;
    height: 190px;
    background: linear-gradient(160deg, #3a3a3a, #111 70%);
    border-radius: 8px;
  }
  .back__url {
    position: absolute;
    left: 0;
    right: 0;
    top: 340px;
    text-align: center;
    font-size: 20px;
    font-weight: 400;
    letter-spacing: 2px;
    color: var(--muted);
  }
</style>
</head>
<body>

<section class="card card--front" aria-label="Business card front">
  <div class="brand">
    <div class="brand__illustration" role="img" aria-label="Black and white illustration of the magician holding a playing card"></div>
    <div class="brand__name">Verlindo Magician</div>
  </div>

  <div class="divider"></div>

  <div class="business">
    <div class="business__title">MAGICIAN VERLINDO</div>
    <div class="business__address">17 rue des Tilleuls - 25000 BESANÇON</div>
  </div>

  <div class="person">
    <div class="person__name">Marc Ravoulet</div>
    <div class="person__role">Magician</div>
    <div class="person__rule"></div>
    <ul class="contact">
      <li>
        <svg viewBox="0 0 16 16"><path fill="#1a1a1a" d="M4 1 6.5 4 5 6c1 2 3 4 5 5l2-1.5L15 12l-2 3C7 14 2 9 1 3z"/></svg>
        0381 946 157
      </li>
      <li>
        <svg viewBox="0 0 16 16"><path fill="#1a1a1a" d="M4 1 6.5 4 5 6c1 2 3 4 5 5l2-1.5L15 12l-2 3C7 14 2 9 1 3z"/></svg>
        0674 219 503
      </li>
      <li>
        <svg viewBox="0 0 16 16"><rect x="1" y="3" width="14" height="10" fill="#1a1a1a"/><path d="M1 3l7 6 7-6" stroke="#fff" stroke-width="1.2" fill="none"/></svg>
        contact@verlindoillusions.example
      </li>
    </ul>
  </div>

  <svg class="band" viewBox="0 0 800 70" preserveAspectRatio="none" aria-hidden="true">
    <polygon points="0,58 400,58 440,12 800,12 800,70 0,70" fill="#e0262c"/>
    <polygon points="452,0 800,0 800,70 0,70 0,64 410,64" fill="#1a1a1a"/>
    <polygon points="0,64 410,64 0,64" fill="#1a1a1a"/>
    <rect x="0" y="64" width="800" height="6" fill="#1a1a1a"/>
  </svg>
  <div class="band__url">www.verlindoillusions.example</div>
</section>

<section class="card card--back" aria-label="Business card back">
  <div class="suit-pattern" role="img" aria-label="Light pattern of playing card suits in pink and grey"></div>
  <div class="back__illustration" role="img" aria-label="Black and white illustration of the magician holding a playing card"></div>
  <div class="back__url">www.verlindoillusions.example</div>
</section>

</body>
</html>
```